Market Compass Web Design

The marketcompassly.com web site will be the source for unbiased economic performance expectations directly from the voice of business owners. Our Market Compass survey effectively asks business owners "How's business?" The web site will present the resultant survey data, graphs, and reports to bankers and business owners. The overall goal is to help bankers better understand businesses of various sizes and industry types, as well as the direction in which our economy is heading by supplying them with the most current possible data.
Updates

Changes have been made to our list of requirements (and list of things the site should NOT include) so please review the briefing again. Thanks!

Reminder: the final deadline for this project isĀ Saturday, February 18, 2012 3:59 AM! Please get your submissions in by that time!

Target Market(s)

Bankers and Business Owners

Industry/Entity Type

Business

Requirements
Must have
• CSS stylesheet, incorporation an Market Compass logo (could be based on the attached example, but rebranding is encouraged), intuitive navigation scheme based on the supplied flow chart, space to incorporate additional sponsor branding and/or advertising in the future
Nice to have
• Space to integrate Google Charts for the graphs representing research data
Should not have
• Incorporated elements from Corvane Insights's main company website - the branding, look, feel, navigation and content of the Market Compass Web site should be completely different and independent

```html
<!DOCTYPE html>
<html lang="en">
<head>
<meta charset="utf-8">
<title>Market Compass</title>
<link rel="stylesheet" href="https://fonts.googleapis.com/css2?family=Open+Sans:ital,wght@0,400;0,600;1,400&family=Kaushan+Script&family=Arimo:wght@400;700&display=swap">
<style>
:root{
  --page:#e3e3e3;
  --ink:#2b2b2b;
  --muted:#555;
  --accent-red:#c8102e;
  --hero-top:#3fb8f2;
  --hero-bottom:#2a98e0;
  --hero-edge:#1b86d0;
  --link:#1a9ad6;
  --heading-blue:#1a6aa8;
  --dark:#232323;
  --footer-link:#6a6a6a;
  --logo-blue:#3a45b0;
}
*{margin:0;padding:0;box-sizing:border-box}
html,body{width:1200px;height:1174px;overflow:hidden}
body{background:var(--page);font-family:"Open Sans",Arial,sans-serif;color:var(--ink);position:relative}
.abs{position:absolute}

/* header */
.logo{left:104px;top:40px;width:300px}
.logo-name{font-size:30px;font-weight:400;color:var(--logo-blue);letter-spacing:1px;line-height:36px}
.logo-sub{font-size:16px;font-weight:400;color:var(--logo-blue);letter-spacing:3px;margin-top:6px}
.account{right:124px;top:12px;font-size:14px;color:var(--accent-red)}
.account span{margin:0 8px;color:var(--accent-red)}
.search{left:779px;top:59px;width:308px;height:32px;display:flex;border:1px solid #9aa;border-radius:4px;overflow:hidden;background:#f4f4f4}
.search-field{flex:1;font-size:11px;color:#333;padding:9px 11px}
.search-btn{width:71px;background:var(--dark);color:#fff;font-size:11px;display:flex;align-items:center;justify-content:center}
.main-nav a{position:absolute;top:126px;font-size:15px;color:var(--ink);text-decoration:none}
.nav-marker{left:649px;top:150px}

/* hero */
.hero{left:0;top:164px;width:1200px;height:337px;background:linear-gradient(var(--hero-top),var(--hero-bottom));border:1px solid var(--hero-edge)}
.hero-title{left:188px;top:218px;font-family:"Kaushan Script",cursive;font-size:36px;color:#111;text-shadow:1px 1px 0 rgba(255,255,255,.4)}
.hero-list{left:186px;top:290px;list-style:none;width:440px}
.hero-list li{position:relative;padding-left:42px;color:#fff;font-size:15px;line-height:24px;margin-bottom:2px}
.hero-list li:nth-child(3){margin-top:9px}
.hero-list svg{position:absolute;left:0;top:4px}
.hero-list u{color:#0b1f3a;text-decoration:underline}
.hero-art{left:700px;top:228px;width:372px;height:250px;background:radial-gradient(ellipse at 60% 45%,#3a1a28 0%,#4a2030 18%,rgba(80,170,225,.6) 45%,rgba(60,160,225,0) 75%)}
.slide-arrow{top:286px}
.pager{left:579px;top:475px;font-size:12px;color:#7cc8f2;letter-spacing:9px}
.pager b{color:#111;font-weight:400}

/* intro & columns */
.intro{left:118px;top:524px;width:950px;font-style:italic;font-size:20px;line-height:24px;color:#444;letter-spacing:.4px}
.feature{width:205px;font-family:Arimo,Arial,sans-serif}
.feature h3{font-size:12.5px;font-weight:400;color:#111;line-height:16px;text-shadow:0 0 .3px #111}
.feature p{font-size:11px;line-height:16px;color:#222}
.feature a{font-size:12.5px;color:var(--link);line-height:18px}
.rule{left:0;top:746px;width:1200px;height:2px;background:#c9c9c9;border-bottom:1px solid #f5f5f5}

/* market status */
.market-title{left:119px;top:771px;font-size:17px;color:var(--heading-blue)}
.market-text{left:122px;top:814px;width:580px;font-family:Arimo,Arial,sans-serif;font-size:11.5px;line-height:18px;letter-spacing:.4px;color:#222}
.market-text p+p{margin-top:18px}

/* contact */
.contact{left:845px;top:762px;width:239px;height:211px;background:#e6e6e6;border:1px solid #fff;border-radius:4px;box-shadow:0 0 0 1px #d0d0d0}
.contact h4{position:absolute;left:16px;top:14px;font-size:12.5px;font-weight:400;color:#111}
.field{position:absolute;left:16px;width:204px;background:#f6f6f6;border:1px solid #d4d4d4;font-size:12.5px;color:#222;padding:8px 10px}
.submit{position:absolute;left:143px;top:179px;width:75px;height:25px;background:#2a2a34;color:#fff;font-size:13px;display:flex;align-items:center;justify-content:center;border:1px solid #555}

/* footer */
.footer{left:0;top:1009px;width:1200px;height:165px;background:var(--dark)}
.footer-nav a{position:absolute;top:14px;font-size:14px;color:var(--footer-link);text-decoration:none}
.copyright{left:117px;top:57px;font-size:10px;color:#fff;letter-spacing:.3px}
.follow{left:896px;top:29px;font-size:9.5px;color:#fff;letter-spacing:.3px}
.social{top:22px;width:24px;height:24px;border-radius:3px}
</style>
</head>
<body>

<header>
  <div class="abs logo">
    <div class="logo-name">MARKET COMPASS</div>
    <div class="logo-sub">CORVANE INSIGHTS</div>
  </div>
  <div class="abs account">Register<span>|</span>Login</div>
  <div class="abs search">
    <div class="search-field">Type your text here</div>
    <div class="search-btn">SEARCH</div>
  </div>
  <nav class="main-nav">
    <a style="left:637px">Home,</a>
    <a style="left:721px">Graphs &amp; Data,</a>
    <a style="left:859px">Info,</a>
    <a style="left:920px">Sponsors,</a>
    <a style="left:1027px">GetMore</a>
  </nav>
  <svg class="abs nav-marker" width="16" height="14"><polygon points="8,0 16,14 0,14" fill="#2fa3e6"/></svg>
</header>

<section class="abs hero">
</section>
<div class="abs hero-title">Market Compass Research</div>
<ul class="abs hero-list">
  <li><svg width="28" height="24"><path d="M2 13 L10 21 L26 3 L22 2 L10 15 L6 10 Z" fill="#fff"/></svg>Lorem Ipsum is simply dummy text of the printing and typesetting industry.</li>
  <li><svg width="28" height="24"><path d="M2 13 L10 21 L26 3 L22 2 L10 15 L6 10 Z" fill="#fff"/></svg>Lorem Ipsum is simply dummy text of the printing</li>
  <li><svg width="28" height="24"><path d="M2 13 L10 21 L26 3 L22 2 L10 15 L6 10 Z" fill="#fff"/></svg>Lorem Ipsum is simply <u>dummy text of the printing</u> and typesetting industry.</li>
</ul>
<div class="abs hero-art" role="img" aria-label="Rising market trend arrow over a perspective grid"></div>
<svg class="abs slide-arrow" style="left:106px" width="22" height="28"><polygon points="20,2 6,14 20,26 14,26 2,14 14,2" fill="#c8102e"/></svg>
<svg class="abs slide-arrow" style="left:1067px" width="22" height="28"><polygon points="2,2 16,14 2,26 8,26 20,14 8,2" fill="#c8102e"/></svg>
<div class="abs pager">1<b>2</b>345</div>

<p class="abs intro">Lorem Ipsum is simply dummy text of the printing and typesetting industry. Lorem Ipsum has been the industry's standard dummy text ever since the 1500s,</p>

<article class="abs feature" style="left:116px;top:612px">
  <h3>Economic Research Data</h3>
  <p>Lorem ipsum dolor sit amet, cons ectetur adipiscing elit. Aliqu am tincidunt mi id libero egestas ut interdum nibh cursus. Aliqu am tincidunt mi id libero egestas ut interdum nibh cursus.</p>
  <a>More &gt;</a>
</article>
<article class="abs feature" style="left:384px;top:612px">
  <h3>Economic Research Data</h3>
  <p>Lorem ipsum dolor sit amet, cons ectetur adipiscing elit. Aliqu am tincidunt mi id libero egestas ut interdum nibh cursus. Aliqu am tincidunt mi id libero egestas ut interdum nibh cursus.</p>
  <a>More &gt;</a>
</article>
<article class="abs feature" style="left:613px;top:603px">
  <h3>Economic Research Data</h3>
  <p>Lorem ipsum dolor sit amet, cons ectetur adipiscing elit. Aliqu am tincidunt mi id libero egestas ut interdum nibh cursus. Aliqu am tincidunt mi id libero egestas ut interdum nibh cursus.</p>
  <a>More &gt;</a>
</article>
<article class="abs feature" style="left:872px;top:596px">
  <h3>Economic Research Data</h3>
  <p>Lorem ipsum dolor sit amet, cons ectetur adipiscing elit. Aliqu am tincidunt mi id libero egestas ut interdum nibh cursus. Aliqu am tincidunt mi id libero egestas ut interdum nibh cursus.</p>
  <a>More &gt;</a>
</article>

<div class="abs rule"></div>

<h2 class="abs market-title" style="font-weight:400">Market Status</h2>
<div class="abs market-text">
  <p>Lorem ipsum dolor sit amet, consectetur adipisicing elit, sed do eiusmod tempor incididunt ut labore et dolore magna aliqua. Ut enim ad minim veniam, quis nostrud exercitation ullamco laboris nisi ut aliquip ex ea commodo consequat.Lorem ipsum dolor sit amet, consectetur adipisicing elit, sed do eiusmod tempor</p>
  <p>&nbsp;incididunt ut labore et dolore magna aliqua. Ut enim ad minim veniam, quis nostrud exercitation ullamco laboris nisi ut aliquip ex ea commodo consequat.</p>
</div>

<form class="abs contact">
  <h4>QUICK CONTACT</h4>
  <div class="field" style="top:39px;height:32px">Name</div>
  <div class="field" style="top:78px;height:33px">Email</div>
  <div class="field" style="top:118px;height:53px;padding-top:6px">Message</div>
  <div class="submit">Submit</div>
</form>

<footer class="abs footer">
  <nav class="footer-nav">
    <a style="left:121px">Home</a>
    <a style="left:201px">Graphs &amp; Data</a>
    <a style="left:334px">Info</a>
    <a style="left:391px">Sponsors</a>
    <a style="left:489px">GetMore</a>
  </nav>
  <div class="abs copyright">© ALL RIGHT RESERVED 2011</div>
  <div class="abs follow">FOLLOW US ON</div>
  <div class="abs social" style="left:999px;background:#2a7fc0"></div>
  <div class="abs social" style="left:1030px;background:#3b5a9a"></div>
  <div class="abs social" style="left:1059px;background:#d8d8d8"></div>
</footer>

</body>
</html>
```